Schlichtes Design für Malerbetrieb
Zielgruppe
Wir sind ein mittelgroßer Malerbetrieb in München mit umfangreichem Leistungsspektrum.
Unsere Hauptleistungen sind: Fassadenrenovierung, Altbausanierung, Betoninstandsetzung, Balkonabdichtung (kein Neubau!).
Unsere Zielgruppen sind: Hausverwaltungen, Firmen und Privatpersonen.
Unsere Kunden schätzen: Konstruktive Organisation und Planung im Vorfeld, Zuverlässigkeit, saubere Arbeitsweise, dauerhafte Balkonabdichtungen.
Aufgabenstellung
Wir möchten eine langlebige, stilvolle, minimalistische Homepage.
Wir möchten von der bestehenden Homepage nur die Schriftart für unseren Firmennamen (Century Gothic) und wenn möglich (nicht zwingend), irgendwo das florale Muster einbauen. Corporate-Design haben wir nicht.
Farbtöne: Firmennamen Orange (hellorange bis erdiges Orange möglich, da sind wir nicht fixiert) , einen dunklen Hintergrundfarbton (Petrol-Blaugrau ?) mit gelbem (neon bis senfgelb) Akzent (Linien), Blumenmuster weiß, grau.
Dies sind nur unsere Ideen. Wir sind aber auch absolut offen für eure Profi-Ideen.
Wir möchten uns von den unzähligen langweiligen 'Pinselseiten mit veralteten Bilder' unserer Kollegen interessant und mit Stil abheben.
Eher nach dem Motto 'weniger ist mehr'.
Einen positiven, sympathischen Eindruck geben und unsere Leistungen in den Vordergrund bringen.
Da wir viele Stammkunden haben, betreiben wir kein Social-Media und möchten dies vorerst auch nicht tun.
Die Seite wird in den nächsten Jahren nicht verändert, höchstens die Bilder aktualisiert.
Die Texte haben wir alle selbst entworfen und möchten wir so übernehmen.
Die Galerien sollen unkompliziert anzuschauen sein.
Uns gefällt die Struktur und Schlichtheit von https://vaartmolen.nl/ oder Timbra.de gut und wir mögen Vintage-Grafiken gerne.
Einerseits darf die Seite geradlinig, andererseits aber auch rund und floral wirken.

```html
<!DOCTYPE html>
<html lang="de">
<head>
<meta charset="utf-8">
<title>kolbrit – Malerbetrieb</title>
<link href="https://fonts.googleapis.com/css2?family=Oswald:wght@300;400&family=Questrial&display=swap" rel="stylesheet">
<style>
  :root {
    --bg-dark: #3d3c3e;
    --navy: #38445d;
    --mustard: #f6b132;
    --slate-grey: #6f6f71;
    --photo-sand: #c9b48a;
    --photo-sky: #8a93a3;
    --text-light: #ffffff;
  }
  html, body {
    margin: 0;
    padding: 0;
    width: 1200px;
    height: 900px;
    overflow: hidden;
    background: var(--bg-dark);
  }
  .page {
    position: relative;
    width: 1200px;
    height: 900px;
    background: var(--bg-dark);
    overflow: hidden;
  }
  .backdrop {
    position: absolute;
    inset: 0;
    width: 1200px;
    height: 900px;
    display: block;
  }
  .main-nav {
    position: absolute;
    top: 62px;
    right: 28px;
    display: flex;
    gap: 17px;
    font-family: "Oswald", sans-serif;
    font-weight: 300;
    font-size: 21px;
    letter-spacing: 0.3px;
    text-transform: uppercase;
    color: var(--text-light);
  }
  .main-nav a, .footer-nav a {
    color: inherit;
    text-decoration: none;
  }
  .brand-name {
    position: absolute;
    left: 106px;
    top: 322px;
    margin: 0;
    font-family: "Questrial", sans-serif;
    font-weight: 400;
    font-size: 134px;
    line-height: 1;
    letter-spacing: 1px;
    color: var(--mustard);
  }
  .footer-nav {
    position: absolute;
    bottom: 16px;
    right: 28px;
    display: flex;
    gap: 16px;
    font-family: "Oswald", sans-serif;
    font-weight: 400;
    font-size: 21px;
    text-transform: uppercase;
    color: var(--text-light);
  }
</style>
</head>
<body>
<div class="page">
  <svg class="backdrop" viewBox="0 0 1024 768" preserveAspectRatio="none" aria-hidden="false">
    <defs>
      <linearGradient id="facade-tones" x1="0" y1="0" x2="0" y2="1">
        <stop offset="0" stop-color="var(--photo-sky)"/>
        <stop offset="0.35" stop-color="#b9ab8c"/>
        <stop offset="1" stop-color="var(--photo-sand)"/>
      </linearGradient>
    </defs>
    <rect class="bg" x="0" y="0" width="1024" height="768" fill="var(--bg-dark)"/>
    <polygon class="navy-wedge" points="0,22 700,368 600,420 320,580 0,425" fill="var(--navy)"/>
    <polygon class="grey-wedge" points="1024,213 600,420 1024,625" fill="var(--slate-grey)"/>
    <polygon class="hero-photo" role="img" aria-label="Foto einer hellen Münchner Altbaufassade mit Mansardendach und Fahnen" points="600,420 1024,625 1024,718 600,718 320,580" fill="url(#facade-tones)"/>
    <polygon class="mustard-wedge" points="0,425 600,718 0,718" fill="var(--mustard)"/>
    <rect class="footer-band" x="0" y="718" width="1024" height="50" fill="var(--bg-dark)"/>
  </svg>

  <nav class="main-nav">
    <a href="#">Malerarbeiten</a>
    <a href="#">Betoninstandsetzung</a>
    <a href="#">Balkonabdichtung</a>
    <a href="#">Farbgestaltung</a>
    <a href="#">Wärmedämmung</a>
    <a href="#">Ausbildung</a>
    <a href="#">Portrait</a>
  </nav>

  <h1 class="brand-name">kolbrit</h1>

  <nav class="footer-nav">
    <a href="#">Kontakt</a>
    <a href="#">Impressum</a>
    <a href="#">Datenschutz</a>
  </nav>
</div>
</body>
</html>
```